Marwick Family Chiropractic Stationary

The letterhead and business card must have our logo.
We would like to see the logo used in different ways ( It can be expanded upon in the stationary.)
Please use the the same or similar colors.
Must be eye catching and memorable.
Must be easy to read

Reason: The doctor has been too busy to make any final decisions. He would like to give himself a little more time.

Target Market(s)

Chiropractic Healthcare

Industry/Entity Type

Business

Requirements
Must have
• Dr. Leonard Marwick D.C.
Chiropractor

860-555-0183

417 Birchfield Road, 2nd Floor
Elmshire, EH 06091

drmarwick@marwickspine.example
www.marwickspine.example
www.facebook.com/MarwickFamilySpine
Should not have
• should not be difficult to read

```html
<!DOCTYPE html>
<html lang="en">
<head>
<meta charset="utf-8">
<title>Marwick Family Chiropractic Stationery</title>
<link href="https://fonts.googleapis.com/css2?family=Montserrat:wght@400;500;700&family=Crimson+Text:wght@400;600;700&display=swap" rel="stylesheet">
<style>
  :root {
    --backdrop: #e8e5e0;
    --ink: #000000;
    --leaf-green: #a5cd5a;
    --leaf-deep: #3f9a3b;
    --leaf-gold: #c9ad3a;
    --trunk: #7d6f61;
    --taupe: #7b6e61;
    --rule: #8c8c8c;
    --text-light: #ffffff;
    --text-grey: #a79d92;
  }
  * { box-sizing: border-box; margin: 0; padding: 0; }
  html, body { width: 1200px; height: 745px; overflow: hidden; }
  body { background: var(--backdrop); position: relative; font-family: "Crimson Text", Georgia, serif; }

  .card { position: absolute; width: 539px; height: 308px; overflow: hidden; box-shadow: 0 2px 6px rgba(0,0,0,.25); }
  .card--front { left: 49px; top: 46px; background: var(--ink); }
  .card--logo { left: 624px; top: 47px; background: var(--ink); }
  .card--wordmark { left: 46px; top: 388px; background: var(--ink); }
  .card--taupe { left: 620px; top: 391px; background: var(--taupe); }

  .band { position: absolute; left: 0; width: 100%; background: var(--leaf-green); }
  .band--top { top: 0; height: 36px; display: flex; align-items: center; justify-content: center; gap: 6px; }
  .band--bottom { bottom: 0; height: 36px; display: flex; align-items: center; justify-content: center; }
  .rule { position: absolute; left: 0; width: 100%; height: 2px; background: var(--rule); }
  .rule--top { top: 40px; }
  .rule--bottom { bottom: 40px; }

  .doctor-name { font-weight: 700; font-size: 19px; color: #1c1c1c; }
  .doctor-title { font-size: 17px; color: #1c1c1c; }
  .address { font-size: 15px; color: #2a2a2a; letter-spacing: .3px; }

  .emblem { position: absolute; left: 50%; transform: translateX(-50%); border-radius: 50% 50% 12px 12px;
            background: radial-gradient(circle at 50% 38%, var(--leaf-gold) 0%, var(--leaf-green) 35%, var(--leaf-deep) 70%, var(--trunk) 100%); }
  .card--front .emblem { top: 50px; width: 110px; height: 110px; }
  .card--logo .emblem { top: 32px; width: 200px; height: 212px; }
  .card--taupe .emblem { top: 30px; width: 200px; height: 214px; background: radial-gradient(circle at 50% 40%, #ffffff 0%, #f1eeea 60%, #d9d3cc 100%); }

  .practice { position: absolute; left: 0; width: 100%; text-align: center; font-family: "Montserrat", Arial, sans-serif; }
  .card--front .practice-name { top: 168px; font-size: 28px; font-weight: 700; color: var(--leaf-green); letter-spacing: 1px; }
  .card--front .practice-sub { top: 204px; font-size: 11.5px; font-weight: 500; color: var(--text-grey); letter-spacing: .6px; }

  .contacts { position: absolute; top: 232px; left: 0; width: 100%; display: flex; justify-content: center; gap: 14px;
              color: var(--text-light); font-size: 14px; align-items: center; white-space: nowrap; }
  .contact { display: flex; align-items: center; gap: 4px; }
  .contact svg { width: 11px; height: 11px; }
  .social-square { width: 9px; height: 9px; background: #4a67ad; display: inline-block; }

  .url { position: absolute; left: 0; width: 100%; text-align: center; font-family: "Montserrat", Arial, sans-serif;
         color: var(--text-light); font-size: 15px; letter-spacing: 2.4px; }
  .card--logo .url, .card--taupe .url { bottom: 20px; }
  .card--wordmark .url { bottom: 28px; }

  .pattern-field { position: absolute; inset: 0; background: radial-gradient(circle, #3a3a1e 0%, #141408 100%); }
  .card--wordmark .practice-name { top: 82px; font-size: 62px; font-weight: 700; color: var(--leaf-green); letter-spacing: 1px; }
  .card--wordmark .practice-sub { top: 162px; font-size: 30px; font-weight: 700; color: var(--text-grey); letter-spacing: 1px; }
</style>
</head>
<body>

<section class="card card--front">
  <div class="band band--top"><span class="doctor-name">Dr. Leonard Marwick D.C.,</span><span class="doctor-title">Chiropractor</span></div>
  <div class="rule rule--top"></div>
  <div class="emblem" role="img" aria-label="Marwick Family Chiropractic tree emblem"></div>
  <div class="practice practice-name">MARWICK</div>
  <div class="practice practice-sub">FAMILY CHIROPRACTIC</div>
  <div class="contacts">
    <span class="contact"><svg viewBox="0 0 12 12"><path d="M2 1h2.5l1 3-1.5 1a7 7 0 0 0 3 3l1-1.5 3 1V10a1 1 0 0 1-1 1A9 9 0 0 1 1 2a1 1 0 0 1 1-1z" fill="#fff"/></svg>860-555-0183</span>
    <span class="contact"><svg viewBox="0 0 12 12"><rect x="1" y="3" width="10" height="7" fill="none" stroke="#fff"/><path d="M1 3l5 4 5-4" fill="none" stroke="#fff"/></svg>mymarwick@marwickspine.example</span>
    <span class="contact"><span class="social-square"></span>MarwickFamilySpine</span>
  </div>
  <div class="rule rule--bottom"></div>
  <div class="band band--bottom"><span class="address">417 Birchfield Road, 2nd Floor, Elmshire, EH 06091</span></div>
</section>

<section class="card card--logo">
  <div class="emblem" role="img" aria-label="Marwick Family Chiropractic tree emblem"></div>
  <div class="url">www.marwickspine.example</div>
</section>

<section class="card card--wordmark">
  <div class="pattern-field" role="img" aria-label="Repeating tree emblem pattern"></div>
  <div class="practice practice-name">MARWICK</div>
  <div class="practice practice-sub">FAMILY CHIROPRACTIC</div>
  <div class="url">www.marwickspine.example</div>
</section>

<section class="card card--taupe">
  <div class="emblem" role="img" aria-label="White tree emblem"></div>
  <div class="url">www.marwickspine.example</div>
</section>

</body>
</html>
```